NZ First of it's kind solutions directory and marketplace for busy Mums needs a business card design

We need a business card design for our new nationwide business in NZ (long term plans to go global). We provide solutions to the everyday challenges that busy Mums face by connecting them with quality communities and suppliers of carefully selected, relevant products and services. We sell direct via our online marketplace. The final design should communicate our values of inclusivity, quality and smart solutions. Colours should incorporate our logo colour palette of #477077 and #6ba8b2. Our website is at https://www.brightnestmums.example

Target Market(s)

busy Mums, Age 28 – 50, female, income over $100K, location main centres NZ primarily but NZ wide. Is likely juggling work or career with a young family. Probably had hobbies which have fallen by the wayside.
-Wants to succeed in her chosen career without compromising on family life
-to successfully juggle her career without feeling like she is compromising her children
- Is time poor, something always has to give and it’s generally her health (she’ll stay up late, get stressed)
- probably ex corporate or professional career. Has discretional income

Industry/Entity Type

Business

Contact Information for Business Card

Lena Forbisher, Founder, BrightNestMums.example (Strapline Tap; Gather; Sorted), 47 Kowhai Terrace, Ellerslie, Auckland 1051, New Zealand. Mob: 021 483 517 Ph: +64 (0)9 571 4860

Font styles to use
Other font styles liked:
• Raleway, and/or Architects Daughter

Colors
00a990
33b8a4
86cfc6
cfeae6

Requirements
Must have
• the above details, streamline. the logo and colours associated with those logos
Should not have
• foil or metallic colours

```html
<!DOCTYPE html>
<html lang="en">
<head>
<meta charset="utf-8">
<title>BrightNestMums – Business Card</title>
<link rel="stylesheet" href="https://fonts.googleapis.com/css2?family=Exo+2:ital,wght@0,600;1,400&family=Roboto+Condensed:wght@400&family=Roboto:wght@400&display=swap">
<style>
  :root {
    --brand-dark: #477077;
    --brand-light: #6ba8b2;
    --band-dark: #3e5b63;
    --ink: #333b3e;
    --card: #fbfbfb;
    --backdrop: #ececec;
  }
  * { box-sizing: border-box; margin: 0; padding: 0; }
  html, body {
    width: 1200px; height: 576px; overflow: hidden;
    background: var(--backdrop);
  }
  .sheet { position: relative; width: 1200px; height: 576px; }

  .card {
    position: absolute; top: 139px;
    width: 484px; height: 293px;
    background: var(--card);
    border-radius: 14px;
    box-shadow: 0 1px 3px rgba(0,0,0,.12);
    overflow: hidden;
  }
  .card--front { left: 82px; }
  .card--back { left: 602px; width: 480px; }

  /* Front */
  .front-mark {
    position: absolute; left: 0; right: 0; top: 62px;
    display: flex; flex-direction: column; align-items: center;
  }
  .brand-dot {
    width: 52px; height: 52px; border-radius: 50%;
    background: var(--brand-dark);
    margin-bottom: 18px;
  }
  .brand-name {
    font-family: "Exo 2", sans-serif; font-weight: 600;
    color: var(--brand-dark);
    letter-spacing: -0.5px; line-height: 1;
  }
  .front-mark .brand-name { font-size: 36px; }
  .strapline {
    margin-top: 10px;
    font-family: "Roboto", sans-serif; font-size: 10px;
    letter-spacing: 4px; color: var(--ink);
  }
  .strapline .divider { color: var(--brand-light); margin: 0 6px; }

  /* Back */
  .back-band { position: absolute; inset: 0 0 auto 0; width: 480px; height: 150px; }
  .holder {
    position: absolute; right: 32px; top: 28px; text-align: right; color: #fff;
  }
  .holder-name { font-family: "Exo 2", sans-serif; font-weight: 600; font-size: 20px; line-height: 1.1; }
  .holder-role { font-family: "Exo 2", sans-serif; font-style: italic; font-size: 11px; margin-top: 2px; }

  .back-mark {
    position: absolute; left: 28px; top: 108px;
    display: flex; align-items: center; gap: 10px;
  }
  .back-mark .brand-dot { width: 30px; height: 30px; margin: 0; }
  .back-mark .brand-name { font-size: 32px; }

  .contacts {
    position: absolute; left: 32px; top: 190px; list-style: none;
    font-family: "Roboto Condensed", sans-serif; font-size: 12px; color: var(--ink);
  }
  .contacts li { display: flex; align-items: center; gap: 9px; height: 18.5px; }
  .contacts svg { width: 9px; height: 9px; fill: var(--brand-dark); flex: none; }

  .address {
    position: absolute; right: 32px; top: 228px; text-align: right;
    font-family: "Roboto Condensed", sans-serif; font-size: 12px; line-height: 18.5px;
    color: var(--ink); font-style: normal;
  }
</style>
</head>
<body>
<main class="sheet">

  <section class="card card--front" aria-label="Card front">
    <div class="front-mark">
      <span class="brand-dot" aria-hidden="true"></span>
      <span class="brand-name">BrightNestMums</span>
      <p class="strapline">TAP<span class="divider">|</span>GATHER<span class="divider">|</span>SORTED</p>
    </div>
  </section>

  <section class="card card--back" aria-label="Card back">
    <svg class="back-band" viewBox="0 0 480 150" aria-hidden="true">
      <path fill="var(--band-dark)" d="M0,0 H480 V121 C380,118 318,52 218,28 C140,10 60,16 0,30 Z"/>
      <path fill="var(--brand-light)" d="M0,40 C90,14 195,18 272,58 C345,96 400,134 480,136 V144 C395,143 340,108 266,72 C190,36 95,38 0,56 Z"/>
    </svg>

    <div class="holder">
      <p class="holder-name">Lena Forbisher</p>
      <p class="holder-role">Founder</p>
    </div>

    <div class="back-mark">
      <span class="brand-dot" aria-hidden="true"></span>
      <span class="brand-name">BrightNestMums</span>
    </div>

    <ul class="contacts">
      <li><svg viewBox="0 0 10 10" aria-hidden="true"><rect x="2.5" y="0" width="5" height="10" rx="1"/></svg>021 483 517</li>
      <li><svg viewBox="0 0 10 10" aria-hidden="true"><path d="M1,3 Q5,0 9,3 L8,4.5 L6.5,4 V3.2 H3.5 V4 L2,4.5 Z M2,5 H8 L9,9 H1 Z"/></svg>+64 (0)9 571 4860</li>
      <li><svg viewBox="0 0 10 10" aria-hidden="true"><path d="M0,2 H10 V8 H0 Z M0.6,2.4 L5,5.6 L9.4,2.4" stroke="#fbfbfb" stroke-width="0.8"/></svg>www.BrightNestMums.example</li>
      <li><svg viewBox="0 0 10 10" aria-hidden="true"><circle cx="5" cy="5" r="4.5"/><path d="M0.5,5 H9.5 M5,0.5 V9.5 M5,0.5 C2,3 2,7 5,9.5 M5,0.5 C8,3 8,7 5,9.5" stroke="#fbfbfb" stroke-width="0.6" fill="none"/></svg>lena@brightnestmums.example</li>
    </ul>

    <address class="address">
      47 Kowhai Terrace, Ellerslie,<br>
      Auckland 1051, New Zealand
    </address>
  </section>

</main>
</body>
</html>
```